New Website Announcement

We need a flyer to announce our new website to customers and prospective clients. The website will be launching soon, but I can provide a detailed outline in PDF form with copy and imagery to serve as inspiration for this design.

I would like a postcard size document that can be mailed in an envelope (no need for postcard style mailer info on 1 side)

About my company:

Verity Lane Studio is a new breed of marketing consulting agency built for the next frontier of consumer learning. Social interaction will be at the heart of great insights going forward – in how consumers engage with brands and in how organizations socialize what they learn to gain competitive advantage.
By fusing innovative insights techniques, technology and compelling graphic design-based reporting, we ensure results get noticed and make an impact.

contact info that can also be included:

Email: marek@veritylane-studio.net

Phone: 518-732-5164

Thanks

Attention all designers submitting a design for this project. Please keep in mind a few important details about this project.

1. Remember that the main objective of this postcard is to announce my new website.

2. Please be sure to read the brief for the copy I would like on each side. You can be creative in how it is displayed, but I need this key information somewhere. All other copy on the attached files is for your background only.

3. Please do not submit overly simple designs that just take the images I provided and overlay a text box with my copy. I could easily do this myself in PowerPoint in 5 minutes.

4. Remember that the design should be edgy and modern but needs to be professional and speak to a business audience.

Please submit any questions. Thank you for your submissions. 

Marek

Target Market(s)

senior level marketing and research clients at large companies and agencies

Industry/Entity Type

Marketing

Requirements
Must have
• Main message:

Need an engaging way to tell customers and prospective clients that we have a new website and that they should come visit us online to learn more about out services, check out case studies and read about our exciting partnerships.

COPY TO USE - UPDATED

Side 1:
(logo)
Introducing Verity Lane Studio

Let’s talk about taking research out of the dark ages.

Visit our newly launched website to learn how and get in touch.

www.veritylane-studio.net

Side 2
Logo
followed by tagline:
Consumer insights that get noticed.
A leading-edge marketing partnership that really works.

Additional text to use on Side 2:
How we can help...

Think of us as your go-to resource for identifying and incorporating the most innovative and exciting techniques into your research programs. We carefully curate and develop close partnerships with the best of the best - from online qualitative research and mobile ethnography to social media listening and fresh takes on concept testing, we can guide the way.

Plus, we believe that socializing consumer learning is just as critical as gathering it.By taking insights deliverables to the next level – through infographics, videos, magazines,interactive profiles and so much more – we are getting stakeholders excited to engage with research and inspired to take action because of it.
It’s a new way to look at insights from a new type of partner. And, it’s a new way to get the most from your research dollars.
Nice to have
• could incorporate our website main image of the lamp on white brick background which is attached, but not 100% mandatory.
Should not have
• - should not be too playful or young, but needs to be modern and design focused

- should not be cluttered or overly 'salesy'

- needs to be upscale and elegant / compelling and aligned with the look and feel of the website imagery (see attached)

```html
<!DOCTYPE html>
<html lang="en">
<head>
<meta charset="utf-8">
<title>Verity Lane Studio – New Website Postcard</title>
<link rel="stylesheet" href="https://fonts.googleapis.com/css2?family=PT+Sans:wght@400;700&family=PT+Sans+Narrow:wght@400;700&family=Questrial&display=swap">
<style>
  :root {
    --page: #ffffff;
    --wall-light: #f6f6f5;
    --wall-mid: #dededd;
    --wall-shade: #c4c4c3;
    --floor-light: #cfcfce;
    --floor-dark: #a3a3a2;
    --glow: rgba(255,255,250,0.95);
    --band: #0b0b0b;
    --brand-blue: #1a78c2;
    --link-blue: #2f6fbf;
    --ink: #1c1c1c;
  }
  * { margin: 0; padding: 0; box-sizing: border-box; }
  html, body {
    width: 1200px; height: 882px; overflow: hidden;
    background: var(--page);
  }
  .canvas { position: relative; width: 1200px; height: 882px; }
  .postcard {
    position: absolute; left: 32px; top: 30px;
    width: 1136px; height: 820px; overflow: hidden;
    box-shadow: 0 2px 8px rgba(0,0,0,0.35);
  }
  .scene-photo {
    position: absolute; inset: 0;
    background:
      radial-gradient(ellipse 260px 200px at 460px 250px, var(--glow) 0%, rgba(255,255,250,0) 100%),
      radial-gradient(ellipse 420px 300px at 0px 0px, rgba(150,150,150,0.35) 0%, rgba(150,150,150,0) 100%),
      radial-gradient(ellipse 260px 40px at 280px 605px, rgba(60,60,60,0.35) 0%, rgba(60,60,60,0) 100%),
      linear-gradient(180deg,
        var(--wall-mid) 0%, var(--wall-light) 22%, var(--wall-light) 45%,
        #e9e9e8 62%, var(--wall-shade) 70%, #b8b8b7 71%,
        var(--floor-light) 71.5%, #bdbdbc 85%, var(--floor-dark) 100%);
  }
  .divider-band {
    position: absolute; left: 0; right: 0; top: 303px; height: 15px;
    background: var(--band);
  }
  .site-url {
    position: absolute; left: 548px; top: 58px;
    font-family: "PT Sans", sans-serif; font-size: 40px; font-weight: 700;
    color: var(--link-blue); letter-spacing: 0.4px; white-space: nowrap;
  }
  .message {
    position: absolute; left: 691px; top: 126px; width: 380px;
    font-family: "PT Sans Narrow", sans-serif; font-size: 29px;
    line-height: 35px; color: var(--ink);
  }
  .message p + p { margin-top: 9px; }
  .brand-block {
    position: absolute; left: 266px; top: 336px;
    font-family: "PT Sans Narrow", sans-serif; font-weight: 700;
    font-size: 80px; line-height: 80px; color: var(--brand-blue);
    text-transform: uppercase; white-space: nowrap;
  }
  .brand-reflection {
    position: absolute; left: 266px; top: 592px;
    font-family: "PT Sans Narrow", sans-serif; font-weight: 700;
    font-size: 80px; line-height: 80px; color: #6b6b6b;
    text-transform: uppercase; white-space: nowrap;
    transform: scaleY(-1); opacity: 0.45;
    -webkit-mask-image: linear-gradient(0deg, #000 0%, rgba(0,0,0,0.5) 45%, transparent 100%);
            mask-image: linear-gradient(0deg, #000 0%, rgba(0,0,0,0.5) 45%, transparent 100%);
  }
  .contact {
    position: absolute; left: 691px; top: 710px;
    font-family: "Questrial", sans-serif; font-size: 18px; color: var(--ink);
    list-style: none;
  }
  .contact li { display: flex; align-items: center; height: 30px; }
  .contact svg { width: 22px; height: 18px; margin-right: 8px; flex: none; }
</style>
</head>
<body>
<div class="canvas">
  <section class="postcard">
    <div class="scene-photo" role="img" aria-label="Photo of an arched black floor lamp lighting a white-painted brick wall above a grey concrete floor"></div>

    <div class="divider-band"></div>

    <div class="site-url">www.veritylane-studio.net</div>

    <div class="message">
      <p>Let’s talk about taking research out of the dark ages.</p>
      <p>Visit our newly launched website to learn how and get in touch.</p>
    </div>

    <h1 class="brand-block">Verity Lane<br>Studio</h1>
    <div class="brand-reflection" aria-hidden="true">Verity Lane<br>Studio</div>

    <ul class="contact">
      <li>
        <svg viewBox="0 0 22 16" aria-hidden="true">
          <rect x="1" y="1" width="20" height="14" fill="none" stroke="#1c1c1c" stroke-width="1.5"/>
          <polyline points="1,1 11,9 21,1" fill="none" stroke="#1c1c1c" stroke-width="1.5"/>
        </svg>
        marek@veritylane-studio.net
      </li>
      <li>
        <svg viewBox="0 0 24 24" aria-hidden="true">
          <path fill="#1c1c1c" d="M6.6 10.8a15.1 15.1 0 0 0 6.6 6.6l2.2-2.2c.3-.3.7-.4 1-.2 1.1.4 2.3.6 3.6.6.6 0 1 .4 1 1V20c0 .6-.4 1-1 1A17 17 0 0 1 3 4c0-.6.4-1 1-1h3.5c.6 0 1 .4 1 1 0 1.3.2 2.5.6 3.6.1.3 0 .7-.2 1z"/>
        </svg>
        518-732-5164
      </li>
    </ul>
  </section>
</div>
</body>
</html>
```